Thornvale Group needs a business card design

We need a new business card design using the logo recently selected in a logo competition on Pixel Bazaar. Our business is a consultancy specializing in aviation and energy and the winning business card design will promote an image of precision and professionalism with creativity.

Please use the logo with the name on the front of the card and use a complementary font. Make the back white with either the light grey or dark grey logo.

Target Market(s)

Senior finance and legal leaders at aviation and energy companies

Industry/Entity Type

Management Consulting

Contact Information for Business Card

Peter Castrell
President
Thornvale Group

www.thornvalegroup.example

(555) 204-6391
pc@thornvalegroup.example

Requirements
Must have
• Professional font that goes well with the logo font

```html
<!DOCTYPE html>
<html lang="en">
<head>
<meta charset="utf-8">
<title>Thornvale Group – Business Card</title>
<link href="https://fonts.googleapis.com/css2?family=Mulish:wght@300;400&display=swap" rel="stylesheet">
<style>
  :root {
    --backdrop: #e6e3de;
    --card-white: #ffffff;
    --card-shade: #f1f1f1;
    --brand-blue: #1d4a7c;
    --brand-blue-light: #2a5c93;
    --text-blue: #2f5d8f;
    --text-grey: #7a7f86;
    --rule-blue: #4d78a8;
    --icon-blue: #3f6a9a;
  }
  * { box-sizing: border-box; margin: 0; padding: 0; }
  html, body {
    width: 1200px; height: 843px; overflow: hidden;
    background: var(--backdrop);
    font-family: "Mulish", Arial, sans-serif;
  }
  .canvas { position: relative; width: 1200px; height: 843px; }

  .card {
    position: absolute;
    box-shadow: 0 10px 28px rgba(0,0,0,.22), 0 2px 6px rgba(0,0,0,.12);
    overflow: hidden;
  }

  /* Back of card */
  .card-back {
    left: 110px; top: 110px; width: 560px; height: 320px;
    background: linear-gradient(160deg, var(--card-white) 55%, var(--card-shade));
    display: flex; align-items: center; justify-content: center;
  }
  .wordmark {
    font-weight: 300;
    text-transform: uppercase;
    letter-spacing: .14em;
    text-align: center;
    line-height: 1.2;
  }
  .card-back .wordmark { color: var(--text-blue); font-size: 34px; }

  /* Front of card */
  .card-front {
    left: 470px; top: 380px; width: 620px; height: 354px;
    background: var(--card-white);
    display: flex;
  }
  .front-brand {
    width: 50%;
    background: linear-gradient(100deg, var(--brand-blue) 40%, var(--brand-blue-light));
    display: flex; align-items: center; justify-content: center;
  }
  .front-brand .wordmark { color: var(--card-white); font-size: 28px; }

  .front-details {
    width: 50%;
    padding: 34px 30px 30px 24px;
    color: var(--text-grey);
    font-weight: 300;
  }
  .person-name {
    color: var(--text-blue);
    font-size: 21px; font-weight: 400;
    letter-spacing: .06em; text-transform: uppercase;
  }
  .person-title { font-size: 15px; margin-top: 2px; color: var(--text-grey); }
  .dotted-rule {
    border: 0; border-top: 2px dotted var(--rule-blue);
    margin: 12px 0 12px;
  }
  .company-lines { font-size: 14.5px; line-height: 1.5; }
  .contact-list { list-style: none; font-size: 15px; line-height: 1.75; }
  .contact-list li { display: flex; align-items: center; gap: 10px; }
  .contact-list svg { width: 13px; height: 13px; fill: var(--icon-blue); flex: none; }
</style>
</head>
<body>
<main class="canvas">

  <section class="card card-back" aria-label="Card back">
    <div class="wordmark">Thornvale<br>Group</div>
  </section>

  <section class="card card-front" aria-label="Card front">
    <div class="front-brand">
      <div class="wordmark">Thornvale<br>Group</div>
    </div>

    <div class="front-details">
      <h1 class="person-name">Peter Castrell</h1>
      <p class="person-title">President</p>
      <hr class="dotted-rule">
      <p class="company-lines">
        Thornvale Group LLC<br>
        Finance and Strategy Consulting<br>
        Aviation - Manufacturing - Energy
      </p>
      <hr class="dotted-rule">
      <ul class="contact-list">
        <li>
          <svg viewBox="0 0 16 16" aria-hidden="true"><path d="M3.6 1.2l2.3 2.6c.4.4.4 1 0 1.4L4.7 6.4c.9 2 2.6 3.7 4.6 4.7l1.2-1.2c.4-.4 1-.4 1.4 0l2.6 2.3c.4.4.4 1 0 1.4l-1.4 1.4C11.4 16.7 6 14 3.4 10.6 1 7.6-.6 4 .8 2.6L2.2 1.2c.4-.4 1-.4 1.4 0z"/></svg>
          (555) 204-6391
        </li>
        <li>
          <svg viewBox="0 0 16 16" aria-hidden="true"><path d="M1 3h14v1.2L8 8.6 1 4.2z"/><path d="M1 5.6l7 4.4 7-4.4V13H1z"/></svg>
          pc@thornvalegroup.example
        </li>
        <li>
          <svg viewBox="0 0 16 16" aria-hidden="true"><circle cx="8" cy="8" r="7"/></svg>
          thornvalegroup.example
        </li>
      </ul>
    </div>
  </section>

</main>
</body>
</html>
```